New Website Design for PHOVAN.org

We are looking for a new website design for PHOVAN.org. PHOVAN is a non profit home inspector association based in California. Home Inspectors are people that come out and look at a house before it's purchased to let the buyer know of any defects that may exist.
Our site is based on Joomla so if you'll be able to make a Joomla 3 template as well, please let us know (not required, but a bonus).
We would like to see designs that incorporate royal blue, white and chrome into the site as that's our main business colors.
We would like a place for rotating banners though they don't need to be the same size as the current site.
We would like navigation to be easier to manage with menus only across the top (via drop down menus) where we are going to sort out the items currently on the side. Possibly the front page could have a graphic link to separate portals for Realtors, Home Buyers and Inspectors, but that's just one option.
We would like a good mobile design or something that will scale easily to mobile.
The Find an Inspector feature is important and should stand out. The ASK PHOVANr site
Current home page feels a bit busy. Would like to simplify a bit.

```html
<!DOCTYPE html>
<html lang="en">
<head>
<meta charset="utf-8">
<title>PHOVAN – Home Inspector Association</title>
<link rel="stylesheet" href="https://fonts.googleapis.com/css2?family=Open+Sans:wght@400;600;700;800&display=swap">
<style>
:root{
  --royal:#3b2f86;
  --royal-dark:#1f2b55;
  --ink:#2b2b2b;
  --muted:#9a9a9a;
  --band:#1b1b1b;
  --page:#ececec;
  --white:#ffffff;
  --line:#e3e3e3;
}
*{box-sizing:border-box;margin:0;padding:0}
html,body{width:877px;height:1200px;overflow:hidden}
body{background:var(--page);font-family:"Open Sans",sans-serif;color:var(--ink);position:relative}
.sheet{position:absolute;left:75px;top:0;width:727px;height:1200px;background:var(--white)}
.abs{position:absolute}

.hero-photo{left:83px;top:0;width:713px;height:408px;background:linear-gradient(100deg,#eef2f6 0%,#d9e3ea 35%,#c9d68a 60%,#9fb4c9 80%,#e6ecf0 100%)}
.nav{left:83px;top:16px;width:698px;height:66px;background:var(--royal)}
.logo{left:94px;top:16px;width:86px;height:66px;background:var(--white);border-radius:0 33px 33px 0;display:flex;align-items:center;justify-content:center;font-size:12px;font-weight:700;color:var(--royal)}
.nav a{position:absolute;top:0;height:66px;line-height:66px;color:var(--white);font-size:9px;text-decoration:none;white-space:nowrap}
.nav a.active{background:var(--royal-dark);width:52px;text-align:center}

.headline{left:98px;top:158px;font-size:29px;font-weight:800;line-height:32px;color:var(--white);letter-spacing:-.3px}
.headline span{color:var(--royal)}
.lede{left:99px;top:230px;width:260px;font-size:13.5px;line-height:18px;color:#222}
.download{left:99px;top:298px;width:176px;height:44px;background:linear-gradient(#fff,#e4e4e4);border-radius:3px;box-shadow:0 1px 3px rgba(0,0,0,.3)}
.download .icon{position:absolute;left:0;top:10px;width:26px;height:24px;background:var(--royal)}
.download .label{position:absolute;left:32px;top:7px;width:140px;font-size:11.5px;line-height:16px;color:#333;text-align:center;font-weight:600}
.dots{left:98px;top:388px;display:flex;gap:2px}
.dots i{width:8px;height:8px;border-radius:50%;background:rgba(255,255,255,.6)}
.dots i.on{background:var(--white)}

.finder{left:80px;top:408px;width:716px;height:84px;background:var(--band)}
.finder label{position:absolute;font-size:8px;color:#ddd;white-space:nowrap}
.finder .field{position:absolute;height:18px;background:var(--white);border:1px solid #ccc}
.search-btn{position:absolute;left:605px;top:32px;width:94px;height:31px;background:var(--royal);border-radius:3px;color:var(--white);font-size:8.5px;font-weight:700;line-height:31px;text-align:center;white-space:nowrap}

.section-title{left:94px;top:516px;font-size:14px;font-weight:400;color:#333}
.card{position:absolute;top:548px;width:220px;height:194px;background:#fafafa;border-bottom:1px solid var(--line)}
.card .photo{height:110px;border:1px solid #ddd}
.card h3{font-size:11.5px;font-weight:400;text-align:center;margin-top:15px;color:#222}
.card p{font-size:8.5px;line-height:11.5px;color:var(--muted);padding:0 16px;margin-top:8px}

.widget{position:absolute;top:771px;height:193px;border:5px solid #ececec;background:var(--white);padding:6px 14px}
.widget h4{font-size:10.5px;font-weight:700;color:#222;margin-bottom:8px}
.links li{list-style:none;font-size:8.5px;color:#333;border-bottom:1px solid var(--line);padding:6px 0 7px;white-space:nowrap}
.viewall{font-size:10.5px;color:var(--royal);text-decoration:underline;margin:6px 0 0 3px;display:block}
.event{font-size:8px;line-height:13px;color:#555;text-align:justify;margin-bottom:8px}
.event u{color:var(--royal);font-weight:600}
.login p{font-size:8px;color:#555}
.login .lbl{font-size:8.5px;color:#444;margin-top:14px}
.login .input{height:19px;border:1px solid #ccc;margin-top:4px;box-shadow:inset 0 1px 2px rgba(0,0,0,.08)}
.login .btn{display:inline-block;margin-top:11px;width:54px;height:22px;background:var(--royal);color:var(--white);font-size:8.5px;line-height:22px;text-align:center}
.login .forgot{position:absolute;right:14px;bottom:10px;font-size:8px;color:var(--royal);text-decoration:underline;font-weight:600}

.footer{left:81px;top:990px;width:715px;height:210px;background:#222;color:#bbb}
.footer h5{position:absolute;top:24px;font-size:12px;font-weight:400;color:var(--white)}
.footer .col{position:absolute;top:52px;font-size:8.5px;line-height:13px;color:#bbb}
.footer .rule{position:absolute;left:0;right:14px;top:168px;border-top:1px solid #3a3a3a}
.footer .copy{position:absolute;left:0;width:100%;top:184px;text-align:center;font-size:7.5px;color:#999}
</style>
</head>
<body>
<div class="sheet"></div>

<div class="abs hero-photo" role="img" aria-label="Photo of two home inspectors in hard hats and safety vests reviewing a site"></div>

<nav class="abs nav">
  <a class="active" style="left:126px">Home</a>
  <a style="left:188px">Find an Inspector</a>
  <a style="left:281px">Home Buyers &amp; Sellers</a>
  <a style="left:401px">Real Estate Agents</a>
  <a style="left:500px">Inspectors</a>
  <a style="left:570px">Ask Phovan</a>
  <a style="left:632px">Conferences</a>
</nav>
<div class="abs logo">PHOVAN</div>

<h1 class="abs headline">OUR REPUTATION<br>IS <span>ROCK SOLID</span></h1>
<p class="abs lede">Le Lorem Ipsum est simplement du faux texte employé dans la composition et la mise en page avant impression.</p>
<div class="abs download">
  <div class="icon"><svg width="26" height="24" viewBox="0 0 26 24"><path d="M9 7l4 4 4-4M9 12l4 4 4-4" fill="none" stroke="#fff" stroke-width="2"/></svg></div>
  <div class="label">DOWNLOAD<br>INFORMATION PACKET</div>
</div>
<div class="abs dots"><i></i><i class="on"></i><i></i></div>

<form class="abs finder">
  <label style="left:16px;top:9px">First Name :</label>
  <div class="field" style="left:17px;top:21px;width:178px"></div>
  <label style="left:16px;top:44px">Last Name :</label>
  <div class="field" style="left:17px;top:56px;width:178px"></div>
  <label style="left:214px;top:9px">Email Address :</label>
  <div class="field" style="left:214px;top:21px;width:178px"></div>
  <label style="left:214px;top:44px">Phone Number :</label>
  <div class="field" style="left:214px;top:56px;width:178px"></div>
  <label style="left:410px;top:9px">Enter Zip Code or Country</label>
  <div class="field" style="left:411px;top:21px;width:178px;height:53px"></div>
  <div class="search-btn">SEARCH INSPECTOR</div>
</form>

<h2 class="abs section-title">What We Do</h2>
<div class="card" style="left:94px">
  <div class="photo" role="img" aria-label="Photo of an inspector in a hard hat checking a building frame" style="background:linear-gradient(90deg,#9bb6cf,#c5a57e 55%,#6f89ad)"></div>
  <h3>PATH TO SUCCESS</h3>
  <p>Lorem Ipsum is simply dummy text of the printing and typesetting industry. Lorem Ipsum has been the industry's standard dummy text</p>
</div>
<div class="card" style="left:328px">
  <div class="photo" role="img" aria-label="Photo of an open book between stacks of books" style="background:linear-gradient(180deg,#6b4a2f,#c9a67a 60%,#8a5a35)"></div>
  <h3>EDUCATIONAL PUBLICATIONS</h3>
  <p>Lorem Ipsum is simply dummy text of the printing and typesetting industry. Lorem Ipsum has been the industry's standard dummy text</p>
</div>
<div class="card" style="left:562px">
  <div class="photo" role="img" aria-label="Illustration of a figure leaning on a red question mark" style="background:radial-gradient(circle at 50% 50%,#e7e7e7,#fff 60%)"></div>
  <h3>ASK PHOVAN</h3>
  <p>Lorem Ipsum is simply dummy text of the printing and typesetting industry. Lorem Ipsum has been the industry's standard dummy text</p>
</div>

<section class="widget" style="left:94px;width:218px">
  <h4>Home Inspection Software</h4>
  <ul class="links">
    <li>California Real Estate Inspection Law</li>
    <li>PHOVAN Chapter Meeting Locations</li>
    <li>Standards of Practice</li>
    <li>Code of Ethics</li>
    <li>Education / CEC's</li>
  </ul>
  <a class="viewall">View All</a>
</section>

<section class="widget" style="left:333px;width:218px">
  <h4>Upcoming Events</h4>
  <p class="event">Lorem ipsum dolor sit amet, consectetuer adipiscing elit, sed diam nonummy nibh euismod tincidunt ut. <u>09-08-2013</u></p>
  <p class="event">Lorem ipsum dolor sit amet, consectetuer adipiscing elit, sed diam nonummy nibh euismod tincidunt. <u>09-08-2013</u></p>
  <p class="event">Lorem ipsum dolor sit amet, consectetuer adipiscing elit, sed diam nonummy nibh euismod tincidunt. <u>09-08-2013</u></p>
</section>

<section class="widget login" style="left:571px;width:211px">
  <h4>Inspector Login</h4>
  <p>Lorem ipsum dolor sit amet, consectetuer</p>
  <div class="lbl">Username</div>
  <div class="input"></div>
  <div class="lbl" style="margin-top:9px">Password</div>
  <div class="input"></div>
  <span class="btn">LOGIN</span>
  <span class="forgot">Forgot Login?</span>
</section>

<footer class="abs footer">
  <h5 style="left:26px">Popular</h5>
  <div class="col" style="left:26px">Inspection FAQs<br>Common Venting of Gas<br>Becoming a Member<br>Education / CECs<br>Affiliate Directory</div>
  <h5 style="left:183px">Business method</h5>
  <div class="col" style="left:183px;width:195px">Ma quande lingues coalesce, li grammatica del resultant lingue es plu simplic e regulari quam ti del coalescent lingues. Li nov lingua franca va esser plu simplic e regulari quam li existent Europan lingues.</div>
  <h5 style="left:427px">Get in touch</h5>
  <div class="col" style="left:427px">2450 Harbor Lane Suite 110<br>Fairview CA 90210-4418<br>Hours: M-F, 8:00am - 5:00pm<br>Phone: (800) 555-0142 or<br>(555) 010-4477<br>Fax: (555) 010-6719<br>Webmaster@PHOVAN.ORG</div>
  <h5 style="left:589px">Who We are</h5>
  <div class="col" style="left:591px;width:100px">Established in 1976, PHOVAN is a non-profit trade association, with chapters located throughout the state. PHOVAN is a member-driven,</div>
  <div class="rule"></div>
  <div class="copy">Copyright © 2013 Phovan. All rights reserved.</div>
</footer>
</body>
</html>
```